Shopping centre customer engagement software website

We need a multi page site with :

*What we do.
*How it works.
*Benefits
* Case study
* Testimonial
* Business login (we provide link to business portal)
* Consumer login (we provide link to consumer site)
* Book a demo
* Contact us

We want it to be clean and crisp and very self explanatory with little clutter. We are thinking white but are open to what ever looks the best.
Updates

Wordpress is preferred

Need extra days to review

Target Market(s)

Shopping centre managers and retail property companies

Coding

Coded - Design and coding required

Number of Pages Required

5+ page

Font styles to use
Sans Serif

Colors
ffffff

Requirements
Must have
• As listed above and must be responsive! Checkout our existing site for the text to be included (will be edited but it’ll give you an idea) www.vostrelink.com

```html
<!DOCTYPE html>
<html lang="en">
<head>
<meta charset="utf-8">
<title>Vostrelink – Shopping Centre Customer Engagement</title>
<link href="https://fonts.googleapis.com/css2?family=Arimo:ital,wght@0,400;0,700;1,400&display=swap" rel="stylesheet">
<style>
:root{
  --red:#b9433b;
  --orange:#e39a45;
  --ink:#1e1e1e;
  --text:#555;
  --muted:#888;
  --line:#d9a7a3;
  --grey-bg:#f1f2f5;
  --white:#ffffff;
  --hero-a:#3a2c22;
  --hero-b:#8a6a48;
}
*{box-sizing:border-box;margin:0;padding:0}
html,body{width:1200px;height:3261px;overflow:hidden}
body{font-family:"Arimo",Helvetica,Arial,sans-serif;color:var(--ink);background:var(--white);position:relative}
.abs{position:absolute}
.red{color:var(--red)}

/* hero */
.hero{left:0;top:0;width:1200px;height:545px;background:linear-gradient(160deg,var(--hero-a),var(--hero-b) 55%,#c9a57c)}
.nav{left:0;top:0;width:1200px;height:70px;display:flex;align-items:center;padding:0 50px}
.brand{color:var(--white);font-size:24px;font-weight:400;white-space:nowrap}
.nav-links{display:flex;gap:34px;margin-left:auto;margin-right:40px}
.nav-links a{color:var(--white);text-decoration:none;font-size:13px;font-weight:700}
.nav-btn{font-size:12px;font-weight:700;border-radius:20px;padding:7px 13px;margin-left:10px;border:2px solid var(--white);text-decoration:none;white-space:nowrap}
.nav-btn.outline{color:var(--white);background:#111}
.nav-btn.solid{color:#111;background:var(--white)}

.subbar{left:0;top:545px;width:1200px;height:32px;background:#eef0f2;display:flex;align-items:center;padding:0 50px;font-size:12px;color:var(--muted)}
.subbar a{color:var(--muted);text-decoration:none;margin-left:18px}
.subbar .socials{margin-left:auto;display:flex;gap:14px;align-items:center}
.subbar .socials span{width:14px;height:14px;border-radius:3px;background:#8a97a8}

.intro{left:0;top:590px;width:1200px;text-align:center}
.intro h1{font-size:23px;font-weight:400;line-height:1.35;color:var(--ink)}
.intro p{font-size:12px;color:var(--text);margin-top:10px}
.demo-btn{display:inline-flex;align-items:center;gap:8px;margin-top:18px;border:2px solid var(--red);border-radius:22px;padding:9px 30px;font-size:12px;font-weight:700;color:var(--red);text-decoration:none}

/* process */
.process{left:0;top:735px;width:1200px;height:410px;background:var(--grey-bg)}
.sec-title{width:1200px;text-align:center;font-size:22px;font-weight:700}
.rule{left:50px;width:1100px;border-top:2px dotted var(--line)}
.step{width:200px;text-align:center}
.step svg{display:block;margin:0 auto}
.step h3{font-size:17px;font-weight:700;margin-top:20px}
.step p{font-size:12px;line-height:1.5;color:var(--text);margin-top:12px}
.connector{height:2px;background:var(--line)}

/* benefits */
.mockup{left:295px;top:1140px;width:605px;height:305px;border-radius:8px;background:linear-gradient(135deg,#f7f7f7,#dfe3e8);box-shadow:0 8px 30px rgba(0,0,0,.18);z-index:2}
.benefits{left:0;top:1344px;width:1200px;height:451px;background:radial-gradient(ellipse at 50% 75%,var(--orange),#cf6a3e 45%,var(--red) 80%)}
.benefits h2{position:absolute;top:148px;width:1200px;text-align:center;color:var(--white);font-size:38px;font-weight:400}
.ben-col{top:230px;width:330px;text-align:center;color:var(--white)}
.ben-col h3{font-size:17px;font-weight:700}
.ben-col p{font-size:12px;line-height:1.55;margin-top:10px}

/* features */
.feature{width:260px;text-align:center}
.feature svg{display:block;margin:0 auto}
.feature h3{font-size:17px;font-weight:700;margin-top:22px}
.feature p{font-size:12px;line-height:1.5;color:var(--text);margin-top:12px}

/* testimonials */
.testimonials{left:0;top:2326px;width:1200px;height:414px;background:var(--grey-bg)}
.quote{font-size:12px;line-height:1.55;font-style:italic;color:var(--text)}
.who{font-size:12px;color:var(--ink);margin-top:10px}
.avatar{width:76px;height:76px;border-radius:50%;background:linear-gradient(135deg,#c9b7a6,#7d6a5c)}

/* contact */
.contact h4{font-size:17px;font-weight:700}
.field{border:1px solid #c9c9c9;border-radius:4px;height:32px;font-size:11px;color:#999;padding:9px 10px;background:var(--white)}
.send{background:var(--red);color:var(--white);font-size:12px;font-weight:700;border-radius:18px;padding:10px 20px;display:inline-block}
.map{left:333px;top:2826px;width:537px;height:224px;background:linear-gradient(135deg,#cfe3ec,#e7e4d8 60%,#bfd9a8)}
.info p{font-size:12px;line-height:1.55;color:var(--text)}
.social-row{display:flex;gap:10px;margin-top:14px}
.social-row span{width:26px;height:26px;border-radius:50%;background:var(--red)}

/* footer */
.footer{left:0;top:3098px;width:1200px;height:163px;border-top:3px solid var(--red)}
.foot-links{display:flex;align-items:center;gap:22px;font-size:12px;font-weight:700}
.foot-small{display:flex;gap:18px;font-size:11px;color:var(--text)}
.foot-brand{right:50px;top:40px;color:#333;font-size:24px}
</style>
</head>
<body>

<header>
  <div class="abs hero" role="img" aria-label="Photograph of a shop front with raised hands holding phones showing the app"></div>
  <nav class="abs nav">
    <div class="brand">Vostrelink</div>
    <div class="nav-links">
      <a href="#">HOW IT WORKS</a><a href="#">BENEFITS</a><a href="#">WHAT WE DO</a><a href="#">CASE STUDY</a>
    </div>
    <a class="nav-btn outline" href="#">Consumer login</a>
    <a class="nav-btn solid" href="#">Business login</a>
  </nav>
  <div class="abs subbar">
    Learn More:<a href="#">Our Company</a><a href="#">Testimonials</a><a href="#">Careers</a><a href="#">Help &amp; Contact</a>
    <div class="socials"><span></span><span></span><span></span>
      <svg width="14" height="14" viewBox="0 0 14 14"><circle cx="6" cy="6" r="4" fill="none" stroke="#8a97a8" stroke-width="2"/><line x1="9" y1="9" x2="13" y2="13" stroke="#8a97a8" stroke-width="2"/></svg>
    </div>
  </div>
</header>

<section class="abs intro">
  <h1>Understanding your customers and identifying trends are key to a successful shopping centre<br>with our innovative and effective services Vostrelink can help you lead the way.</h1>
  <p>See some of the features below and learn why businesses trust Vostrelink</p>
  <a class="demo-btn" href="#"><svg width="10" height="10" viewBox="0 0 10 10"><path d="M1 0 L9 5 L1 10Z" fill="#b9433b"/></svg>BOOK A DEMO</a>
</section>

<section class="abs process">
  <h2 class="abs sec-title" style="top:32px">Our <span class="red">Process</span></h2>
  <div class="abs rule" style="top:64px"></div>

  <div class="abs connector" style="left:210px;top:160px;width:105px"></div>
  <div class="abs connector" style="left:434px;top:160px;width:105px"></div>
  <div class="abs connector" style="left:658px;top:160px;width:105px"></div>
  <div class="abs connector" style="left:884px;top:160px;width:105px"></div>

  <div class="abs step" style="left:50px;top:125px">
    <svg width="72" height="72" viewBox="0 0 72 72" fill="none" stroke="#b9433b" stroke-width="2"><rect x="10" y="24" width="46" height="32" rx="4"/><rect x="20" y="14" width="40" height="26" rx="3" transform="rotate(-12 40 27)"/><rect x="40" y="34" width="20" height="12" rx="2"/></svg>
    <h3>Allocate Cards</h3><p>Nemo enim ipsam voluptatem quia voluptas sit aspernatur aut odit aut fugit.</p>
  </div>
  <div class="abs step" style="left:274px;top:125px">
    <svg width="72" height="72" viewBox="0 0 72 72" fill="none" stroke="#b9433b" stroke-width="2"><path d="M10 30 H62 L56 60 H16 Z"/><path d="M22 30 Q36 6 50 30"/><line x1="26" y1="38" x2="26" y2="52"/><line x1="36" y1="38" x2="36" y2="52"/><line x1="46" y1="38" x2="46" y2="52"/></svg>
    <h3>Direct Marketing</h3><p>Nemo enim ipsam voluptatem quia voluptas sit aspernatur aut odit aut fugit.</p>
  </div>
  <div class="abs step" style="left:498px;top:125px">
    <svg width="72" height="72" viewBox="0 0 72 72" fill="none" stroke="#b9433b" stroke-width="2"><rect x="26" y="8" width="22" height="38" rx="3"/><line x1="33" y1="40" x2="41" y2="40"/><path d="M22 40 Q18 52 28 64 H46 Q52 54 50 44"/></svg>
    <h3>Rewarding Loyalty</h3><p>Nemo enim ipsam voluptatem quia voluptas sit aspernatur aut odit aut fugit.</p>
  </div>
  <div class="abs step" style="left:724px;top:125px">
    <svg width="72" height="72" viewBox="0 0 72 72" fill="none" stroke="#b9433b" stroke-width="2"><rect x="12" y="22" width="44" height="30" rx="3"/><line x1="12" y1="32" x2="56" y2="32"/><path d="M22 22 L40 8 L50 22"/><circle cx="50" cy="52" r="9"/><line x1="50" y1="47" x2="50" y2="57"/><line x1="45" y1="52" x2="55" y2="52"/></svg>
    <h3>Collect Data</h3><p>Nemo enim ipsam voluptatem quia voluptas sit aspernatur aut odit aut fugit.</p>
  </div>
  <div class="abs step" style="left:946px;top:125px">
    <svg width="72" height="72" viewBox="0 0 72 72" fill="none" stroke="#b9433b" stroke-width="2"><path d="M58 36 A22 22 0 1 1 48 17"/><polyline points="42,12 50,16 46,24"/><path d="M36 36 L52 28"/><circle cx="36" cy="36" r="3"/></svg>
    <h3>Data Analytics</h3><p>Nemo enim ipsam voluptatem quia voluptas sit aspernatur aut odit aut fugit.</p>
  </div>
</section>

<div class="abs mockup" role="img" aria-label="Laptop and phone screens showing the shopping cart and loyalty app"></div>

<section class="abs benefits">
  <h2>The benefits provided by Vostrelink</h2>
  <div class="abs ben-col" style="left:60px">
    <h3>Example Scenario</h3>
    <p><b>Vostrelink can predict more accurately and more reliably than ever before that on a cold wet Thursday next week: 35% of a retailers customers coming through their doors will be women aged between 30-35 looking to buy kids wear. When they arrive Vostrelink can identify them personally and send them messages based on where they are and their preferences.</b></p>
  </div>
  <div class="abs ben-col" style="left:435px">
    <h3>Millbrook Centre Manager</h3>
    <p>All of the data captured has now been analysed, equipping us with invaluable insights into shopping and spending patterns, and the impact of our media campaigns – all of which is gold dust as we plan ahead for future focussed campaigns. The flexibility of the Vostrelink operating platform software means we will most certainly use this system again going forward.</p>
  </div>
  <div class="abs ben-col" style="left:810px">
    <h3>Shopping Centres Real Time</h3>
    <p>Vostrelink gives shopping centres real time tracking through smart ID's of individual customer journeys through their physical stores, enabling highly targeted, relevant and timely promotional and rewarding capabilities. Furthermore, through deep analytical data processing of the customer journey, centre managers will be able to more accurately and reliably predict shopping behaviours.</p>
  </div>
</section>

<section class="abs" style="left:0;top:1795px;width:1200px;height:531px">
  <h2 class="abs sec-title" style="top:30px">Our <span class="red">Features</span></h2>
  <div class="abs rule" style="top:62px"></div>

  <div class="abs feature" style="left:50px;top:105px">
    <svg width="52" height="52" viewBox="0 0 52 52" fill="none" stroke="#b9433b" stroke-width="2"><rect x="4" y="4" width="44" height="44" rx="2"/><line x1="4" y1="16" x2="48" y2="16"/><line x1="22" y1="16" x2="22" y2="48"/><line x1="22" y1="32" x2="48" y2="32"/></svg>
    <h3>Graphical Dashboard</h3><p>Sed ut perspiciatis unde omnis iste natus error sit voluptate accusantium doloremqu.</p>
  </div>
  <div class="abs feature" style="left:330px;top:105px">
    <svg width="52" height="52" viewBox="0 0 52 52" fill="none" stroke="#b9433b" stroke-width="2"><rect x="4" y="4" width="44" height="44" rx="2"/><line x1="4" y1="12" x2="48" y2="12"/><circle cx="26" cy="26" r="6"/><path d="M16 42 Q26 30 36 42"/></svg>
    <h3>Member Portal</h3><p>Nemo qui enim ipsam voluptatem quia voluptas sit aspernatur aut odit aut fugit.</p>
  </div>
  <div class="abs feature" style="left:610px;top:105px">
    <svg width="52" height="52" viewBox="0 0 52 52" fill="none" stroke="#b9433b" stroke-width="2"><circle cx="26" cy="12" r="6"/><path d="M16 30 Q26 16 36 30 L26 48 Z"/><line x1="6" y1="40" x2="18" y2="34"/><line x1="46" y1="40" x2="34" y2="34"/></svg>
    <h3>Lead Management</h3><p>Sed ut perspiciatis unde omnis iste natus error sit voluptate accusantium quido et.</p>
  </div>
  <div class="abs feature" style="left:890px;top:105px">
    <svg width="52" height="52" viewBox="0 0 52 52"><circle cx="26" cy="26" r="22" fill="#b9433b"/><circle cx="26" cy="26" r="9" fill="none" stroke="#fff" stroke-width="2"/><circle cx="26" cy="26" r="3" fill="#fff"/></svg>
    <h3>CRM</h3><p>Ut enim ad minim veniam, quis nostrud etor exercitation ullamco laboris nisi ut aliquipe.</p>
  </div>

  <div class="abs feature" style="left:50px;top:305px">
    <svg width="52" height="52" viewBox="0 0 52 52" fill="none" stroke="#b9433b" stroke-width="3"><circle cx="18" cy="26" r="13"/><circle cx="34" cy="26" r="13"/></svg>
    <h3>Billing Subscription</h3><p>Sed ut perspiciatis unde omnis iste natus error sit voluptate accusantium doloremqu.</p>
  </div>
  <div class="abs feature" style="left:330px;top:305px">
    <svg width="52" height="52" viewBox="0 0 52 52" fill="none" stroke="#b9433b" stroke-width="2"><rect x="4" y="10" width="44" height="32" rx="3"/><rect x="4" y="16" width="44" height="6" fill="#b9433b"/><line x1="10" y1="32" x2="24" y2="32"/></svg>
    <h3>Payment Gateway</h3><p>Nemo qui enim ipsam voluptatem quia voluptas sit aspernatur aut odit aut fugit.</p>
  </div>
  <div class="abs feature" style="left:610px;top:305px">
    <svg width="52" height="52" viewBox="0 0 52 52" fill="none" stroke="#b9433b" stroke-width="2"><path d="M10 4 H34 L44 14 V48 H10 Z"/><line x1="16" y1="20" x2="36" y2="20"/><rect x="14" y="28" width="26" height="12" fill="#b9433b"/></svg>
    <h3>Invoicing</h3><p>Sed ut perspiciatis unde omnis iste natus error sit voluptate accusantium quido et.</p>
  </div>
  <div class="abs feature" style="left:890px;top:305px">
    <svg width="52" height="52" viewBox="0 0 52 52" fill="none" stroke="#b9433b" stroke-width="2"><path d="M26 4 Q36 14 34 34 H18 Q16 14 26 4 Z"/><circle cx="26" cy="20" r="4"/><path d="M18 30 L12 40 L18 38"/><path d="M34 30 L40 40 L34 38"/><line x1="26" y1="38" x2="26" y2="48"/></svg>
    <h3>Commission Tracking</h3><p>Duis aute irure dolor in reprehenderit in ter voluptate velit esse cillum dolore eu fugiat.</p>
  </div>
</section>

<section class="abs testimonials">
  <h2 class="abs sec-title" style="top:36px">What <span class="red">People Say</span></h2>
  <div class="abs rule" style="top:68px"></div>
  <div class="abs" style="left:600px;top:120px;height:260px;border-left:2px dotted var(--line)"></div>
  <div class="abs" style="left:50px;top:228px;width:1100px;border-top:2px dotted var(--line)"></div>

  <div class="abs" style="left:55px;top:128px;width:410px;text-align:right">
    <p class="quote">Duis aute irure dolor in reprehenderit in voluptate velit esse cillum dolore eu fugiat nulla pariatur. Excepteur sint occaecat cupidatat non proident, sunt in culpa qui officia deserunt mollit.</p>
    <p class="who">Owen Marsh, Operations Manager</p>
  </div>
  <div class="abs avatar" style="left:494px;top:128px" role="img" aria-label="Portrait of Owen Marsh"></div>

  <div class="abs avatar" style="left:632px;top:128px" role="img" aria-label="Portrait of Clara Voss"></div>
  <div class="abs" style="left:740px;top:128px;width:410px">
    <p class="quote">Provident, similique sunt in culpa qui officia deserunt mollitia animi, id est laborum et dolorum fuga. Et harum quidem rerum facilis est et expedita distinctio. Nam libero tempore, cum soluta nobis.</p>
    <p class="who">Clara Voss, Creative Designer</p>
  </div>

  <div class="abs" style="left:55px;top:270px;width:410px;text-align:right">
    <p class="quote">Luis aute irure dolor in reprehenderit in pluptate velit esse cillum dolore eu fugiat nulla pariatur. Excepteur sint occaecat cupidatat non proident, sunt in culpa qui officia deserunt mollit.</p>
    <p class="who">Nina Holt, Manager</p>
  </div>
  <div class="abs avatar" style="left:494px;top:268px" role="img" aria-label="Portrait of Nina Holt"></div>

  <div class="abs avatar" style="left:632px;top:268px" role="img" aria-label="Portrait of Reid Calloway"></div>
  <div class="abs" style="left:740px;top:270px;width:410px">
    <p class="quote">At vero eos et accusamus et iusto odio dignissimos ducimus qui blanditiis praesentium voluptatum deleniti atque corrupti quos dolores et quas molestias excepturi sint occaecati asperiores.</p>
    <p class="who">Reid Calloway, Developer</p>
  </div>
</section>

<section class="abs contact" style="left:0;top:2740px;width:1200px;height:358px">
  <h4 class="abs" style="left:52px;top:42px">Feel Free to Mail</h4>
  <div class="abs field" style="left:52px;top:86px;width:118px">Name *</div>
  <div class="abs field" style="left:188px;top:86px;width:118px">Email *</div>
  <div class="abs field" style="left:52px;top:134px;width:254px">Subject</div>
  <div class="abs field" style="left:52px;top:182px;width:254px;height:70px">Write Your Message Here...</div>
  <div class="abs send" style="left:52px;top:275px">SEND MESSAGE</div>

  <h4 class="abs" style="left:333px;top:48px;width:537px;text-align:center">Headquarters</h4>

  <div class="abs info" style="left:896px;top:42px;width:270px">
    <h4>Contact Info</h4>
    <p style="margin-top:16px">Our staff is available to you from 9AM until 5PM on weekdays.</p>
    <p style="margin-top:12px">Phone: +44 (020) 014 73 59</p>
    <p style="margin-top:8px">Office: Unit 7, Harbour Road, Dunmore, DN4 2RL</p>
    <p style="margin-top:8px">Email: hello@vostrelink.com</p>
    <h4 style="margin-top:14px">Follow Us On</h4>
    <div class="social-row"><span></span><span></span><span></span><span></span><span></span></div>
  </div>
</section>
<div class="abs map" role="img" aria-label="Street map showing the headquarters location"></div>

<footer class="abs footer">
  <div class="abs foot-links" style="left:52px;top:50px">
    <svg width="14" height="14" viewBox="0 0 14 14"><circle cx="6" cy="6" r="4" fill="none" stroke="#333" stroke-width="2"/><line x1="9" y1="9" x2="13" y2="13" stroke="#333" stroke-width="2"/></svg>
    <span>Help &amp; Contact</span><span>Benefits</span><span>Case study</span><span>How it works</span>
  </div>
  <div class="abs brand foot-brand">Vostrelink</div>
  <div class="abs foot-small" style="left:52px;top:96px">
    <span>About</span><span>Blog</span><span>Careers</span><span>Public Policy</span><span>What we do</span><span>Testimonials</span><span>Partners</span>
  </div>
  <div class="abs foot-small" style="left:902px;top:96px">
    <span>© 2006 - 2018</span><span>Privacy</span><span>Legal</span><span>Feedback</span>
  </div>
  <div class="abs" style="left:0;top:154px;width:1200px;height:6px;background:var(--red)"></div>
</footer>

</body>
</html>
```